Business Card Design

We need a design for business cards for our company. We have a logo. We teach EMT's and we are based out of Virginia. The information that will need to add would be, name, title, phone number, email, address. On the back of the business card would be "We help you, help others"

Target Market(s)

People that want to become EMT's

Colors

Designer to choose colors to be used in the design.

Requirements
Must have
• company logo

```html
<!DOCTYPE html>
<html lang="en">
<head>
<meta charset="utf-8">
<title>Crestline Medic Training — Business Card</title>
<link rel="stylesheet" href="https://fonts.googleapis.com/css2?family=Source+Sans+3:wght@400;600&display=swap">
<style>
  :root {
    --board: #dcdddf;
    --card-dark: #1f2a35;
    --card-light: #ffffff;
    --band: #5f6c79;
    --band-ink: #17202a;
    --brand-red: #e0263f;
    --slate: #6f7b87;
    --slate-light: #8a96a2;
    --rule: #4b5662;
    --label: #3a3f45;
    --marker: #6e7378;
  }
  * { box-sizing: border-box; margin: 0; padding: 0; }
  html, body { width: 1200px; height: 1200px; overflow: hidden; }
  body {
    background: var(--board);
    font-family: "Source Sans 3", "Myriad Pro", sans-serif;
    position: relative;
  }
  .card {
    position: absolute;
    left: 361px;
    width: 474px;
    height: 269px;
    overflow: hidden;
    box-shadow: 0 14px 18px -8px rgba(0,0,0,0.35);
  }
  .card--front { top: 236px; background: var(--card-dark); }
  .card--back { top: 532px; background: var(--card-light); }

  .wordmark {
    position: absolute;
    left: 0; right: 0;
    display: flex;
    justify-content: center;
    align-items: center;
    gap: 10px;
  }
  .wordmark__dot {
    width: 14px; height: 14px;
    border-radius: 50%;
    background: var(--brand-red);
  }
  .wordmark__name {
    font-weight: 600;
    font-size: 30px;
    letter-spacing: 0.5px;
    color: var(--brand-red);
    line-height: 1;
  }
  .card--front .wordmark { top: 60px; }
  .card--back .wordmark { top: 56px; }

  .holder {
    position: absolute;
    top: 165px; left: 0; right: 0;
    display: flex;
    align-items: center;
    gap: 10px;
  }
  .holder__rule { flex: 1; height: 1px; background: var(--brand-red); }
  .holder__name {
    font-weight: 600;
    font-size: 13.5px;
    color: var(--slate);
    white-space: nowrap;
  }
  .holder__title {
    position: absolute;
    top: 186px; left: 0; right: 0;
    text-align: center;
    font-size: 11px;
    color: var(--slate);
  }
  .contact-band {
    position: absolute;
    left: 0; right: 0; bottom: 0;
    height: 34px;
    background: var(--band);
    display: flex;
    align-items: center;
    justify-content: space-between;
    padding: 0 10px;
    color: var(--band-ink);
    font-size: 10.5px;
  }
  .contact-band__item { display: flex; align-items: center; gap: 4px; white-space: nowrap; }
  .contact-band__item--address { font-size: 9px; }
  .contact-band svg { fill: #ffffff; }

  .tagline {
    position: absolute;
    top: 164px; left: 0; right: 0;
    display: flex;
    align-items: center;
    gap: 8px;
  }
  .tagline__rule { flex: 1; height: 1px; background: var(--rule); }
  .tagline__text { font-size: 17.5px; color: var(--slate); white-space: nowrap; }

  .side-label {
    position: absolute;
    left: 899px;
    display: flex;
    align-items: center;
    gap: 6px;
    font-size: 14.5px;
    color: var(--label);
  }
  .side-label--front { top: 357px; }
  .side-label--back { top: 643px; }
  .side-label svg { fill: var(--marker); }
</style>
</head>
<body>

  <section class="card card--front" aria-label="Card front">
    <div class="wordmark">
      <span class="wordmark__dot"></span>
      <span class="wordmark__name">CRESTLINE MEDIC</span>
    </div>
    <div class="holder">
      <span class="holder__rule"></span>
      <span class="holder__name">Dana Whitfield, LCSW, LAADC</span>
      <span class="holder__rule"></span>
    </div>
    <p class="holder__title">Director &amp; Founder | &nbsp;Interventionist</p>
    <div class="contact-band">
      <span class="contact-band__item">
        <svg width="12" height="12" viewBox="0 0 24 24" aria-hidden="true"><path d="M6.6 10.8a15.1 15.1 0 0 0 6.6 6.6l2.2-2.2c.3-.3.7-.4 1-.2 1.1.4 2.3.6 3.6.6.6 0 1 .4 1 1V20c0 .6-.4 1-1 1C10.6 21 3 13.4 3 4c0-.6.4-1 1-1h3.5c.6 0 1 .4 1 1 0 1.3.2 2.5.6 3.6.1.3 0 .7-.2 1z"/></svg>
        555-014-2290
      </span>
      <span class="contact-band__item">
        <svg width="13" height="10" viewBox="0 0 26 20" aria-hidden="true"><path d="M0 0h26v20H0z M2 2v1l11 8 11-8V2z" fill-rule="evenodd"/></svg>
        dana@crestlinemedic.com
      </span>
      <span class="contact-band__item contact-band__item--address">
        <svg width="11" height="12" viewBox="0 0 24 24" aria-hidden="true"><path d="M12 1a9 9 0 0 0-9 9c0 6.5 9 13 9 13s9-6.5 9-13a9 9 0 0 0-9-9zm0 12a3 3 0 1 1 0-6 3 3 0 0 1 0 6z"/></svg>
        Suite 14, 880 Harbor Street, Richmond
      </span>
    </div>
  </section>

  <section class="card card--back" aria-label="Card back">
    <div class="wordmark">
      <span class="wordmark__dot"></span>
      <span class="wordmark__name">CRESTLINE MEDIC</span>
    </div>
    <div class="tagline">
      <span class="tagline__rule"></span>
      <span class="tagline__text">We help you, help others</span>
      <span class="tagline__rule"></span>
    </div>
  </section>

  <div class="side-label side-label--front">
    <svg width="12" height="24" viewBox="0 0 12 24" aria-hidden="true"><path d="M12 0v24L0 12z"/></svg>
    Front side
  </div>
  <div class="side-label side-label--back">
    <svg width="12" height="24" viewBox="0 0 12 24" aria-hidden="true"><path d="M12 0v24L0 12z"/></svg>
    Back side
  </div>

</body>
</html>
```